Road Construction Company needs business cards

We would like a new business card designed for our business.

We're a road construction company based in Qld, Australia.

Can the business card please have the following information on it.

Name: Warren Halbeck
Position: General Manager
Phone: 0472 915 348
Email: Warren.halbeck@tovrin.com.au
Address: 87 Marrow Ave, Pendlebay, QLD, 4023
Website: www.tovrin.com.au

Visually we'd like the card to be professional and simple.

Attached is our logo.

Our website is www.tovrin.com.au

Target Market(s)

Men aged 25-60

Contact Information for Business Card

As listed in project description

Font styles to use
Serif

Requirements
Must have
• Large logo on back of card

```html
<!DOCTYPE html>
<html lang="en">
<head>
<meta charset="utf-8">
<title>Tovrin Business Card</title>
<link rel="stylesheet" href="https://fonts.googleapis.com/css2?family=Fira+Sans:wght@400;600;800&display=swap">
<style>
  :root {
    --backdrop: #909396;
    --card-blue: #0254a4;
    --accent-blue: #3aa0dc;
    --white: #ffffff;
  }
  * { margin: 0; padding: 0; box-sizing: border-box; }
  html, body {
    width: 1200px; height: 1200px; overflow: hidden;
    background: var(--backdrop);
    font-family: "Fira Sans", sans-serif;
  }
  .canvas { position: relative; width: 1200px; height: 1200px; }
  .card {
    position: absolute;
    width: 635px; height: 404px;
    background: var(--card-blue);
    color: var(--white);
  }
  .card--front { left: 155px; top: 150px; }
  .card--back { left: 373px; top: 672px; }

  .brand-name {
    position: absolute; left: 0; right: 0; top: 150px;
    text-align: center;
    font-weight: 800; font-size: 60px; letter-spacing: 2px;
    line-height: 1;
    color: var(--white);
  }

  .contact-name {
    position: absolute; left: 0; right: 0; top: 90px;
    text-align: center; font-weight: 600; font-size: 23px; letter-spacing: 0.3px;
  }
  .contact-role {
    position: absolute; left: 0; right: 0; top: 119px;
    text-align: center; font-weight: 400; font-size: 18px;
    color: var(--accent-blue);
  }
  .icon-rail { position: absolute; left: 152px; top: 156px; }
  .contact-list {
    position: absolute; left: 0; right: 0; top: 205px;
    list-style: none; text-align: center;
    font-size: 15.5px; line-height: 27.7px; letter-spacing: 0.2px;
  }
</style>
</head>
<body>
<main class="canvas">
  <section class="card card--front" aria-label="Card front">
    <h1 class="brand-name">TOVRIN</h1>
  </section>

  <section class="card card--back" aria-label="Card back">
    <h2 class="contact-name">WARREN HALBECK</h2>
    <p class="contact-role">General Manager</p>

    <svg class="icon-rail" width="328" height="40" viewBox="0 0 328 40" aria-hidden="true">
      <g stroke="var(--white)" stroke-width="2" fill="none">
        <line x1="0" y1="20" x2="78" y2="20"/>
        <line x1="110" y1="20" x2="124" y2="20"/>
        <line x1="156" y1="20" x2="170" y2="20"/>
        <line x1="202" y1="20" x2="217" y2="20"/>
        <line x1="249" y1="20" x2="328" y2="20"/>
        <circle cx="94" cy="20" r="15.5"/>
        <circle cx="140" cy="20" r="15.5"/>
        <circle cx="186" cy="20" r="15.5"/>
        <circle cx="233" cy="20" r="15.5"/>
      </g>
      <g fill="var(--accent-blue)">
        <path d="M86 19 q8 -6 16 0 l-1.5 2.5 h-2.5 l-1 -2 h-6 l-1 2 h-2.5 z"/>
        <rect x="89" y="21" width="10" height="5" rx="1"/>
        <rect x="133" y="15" width="14" height="10" rx="1"/>
      </g>
      <polyline points="133,15.5 140,21 147,15.5" stroke="var(--card-blue)" stroke-width="1.3" fill="none"/>
      <g stroke="var(--accent-blue)" stroke-width="1.4" fill="none">
        <circle cx="185" cy="19" r="6.5"/>
        <ellipse cx="185" cy="19" rx="2.8" ry="6.5"/>
        <line x1="178.5" y1="19" x2="191.5" y2="19"/>
      </g>
      <path d="M187 20 l6 2.5 -2.5 1 2 3 -1.3 0.8 -2 -3 -1.6 2 z" fill="var(--accent-blue)"/>
      <path d="M233 28 q-6 -7 -6 -11 a6 6 0 0 1 12 0 q0 4 -6 11 z" fill="var(--accent-blue)"/>
      <circle cx="233" cy="17" r="2.2" fill="var(--card-blue)"/>
    </svg>

    <ul class="contact-list">
      <li>0472 915 348</li>
      <li>Warren.halbeck@tovrin.com.au</li>
      <li>www.tovrin.com.au</li>
      <li>87 Marrow Ave, Pendlebay, QLD, 4023</li>
    </ul>
  </section>
</main>
</body>
</html>
```